BrindleStaffing Business Card Design

We are a staffing company finding positions for dedicated nurses and physicians.

Target Market(s)

Business Professionals

Industry/Entity Type

Staffing

Contact Information for Business Card

Gordon Pratley
Chairman
417 39th Avenue South
SAINT PETERSBURG FL 33712
813-555-4172 Mobile
813-555-8036 Fax
gpratley@brindlestaffing.com
www.brindlestaffing.com

Font styles to use
Sans Serif

Colors
fbee3e
f04a50
f37122

Requirements
Must have
• Logo Attached, see colors below. We'd like to see Yellow, Orange and Red.

```html
<!DOCTYPE html>
<html lang="en">
<head>
<meta charset="utf-8">
<title>BrindleStaffing Business Card</title>
<link rel="stylesheet" href="https://fonts.googleapis.com/css2?family=Open+Sans:wght@400;600;700&family=Poppins:wght@700&display=swap">
<style>
  :root {
    --backdrop: #2a2a2a;
    --card: #1b1b1d;
    --ink: #f2f2f2;
    --muted: #c9c9c9;
    --brand-yellow: #fbee3e;
    --brand-orange: #f37122;
    --brand-red: #f04a50;
    --divider: #6a6a6a;
  }
  * { margin: 0; padding: 0; box-sizing: border-box; }
  html, body { width: 1200px; height: 960px; overflow: hidden; background: var(--backdrop); }
  body { position: relative; font-family: "Open Sans", sans-serif; color: var(--ink); }

  .card {
    position: absolute;
    left: 280px;
    width: 640px;
    height: 366px;
    background: var(--card);
    border-radius: 4px;
    overflow: hidden;
    box-shadow: 0 10px 30px rgba(0,0,0,.45);
  }
  .card--front { top: 70px; }
  .card--back { top: 520px; }

  .texture { position: absolute; inset: 0; background: radial-gradient(ellipse at 50% 40%, #2b2b2e 0%, var(--card) 75%); }

  .wordmark {
    position: absolute;
    display: flex;
    align-items: center;
    gap: 10px;
    font-family: "Poppins", sans-serif;
    font-weight: 700;
    color: var(--brand-orange);
    letter-spacing: -0.5px;
    white-space: nowrap;
  }
  .wordmark__dot { width: 14px; height: 14px; border-radius: 50%; background: var(--brand-yellow); }

  .card--front .wordmark { left: 0; right: 0; top: 120px; justify-content: center; font-size: 52px; }
  .front-url {
    position: absolute; left: 0; right: 0; top: 205px;
    text-align: center; font-size: 19px; letter-spacing: 2px; color: var(--ink);
  }

  .card--back .wordmark { left: 250px; top: 50px; font-size: 40px; }

  .address {
    position: absolute; left: 40px; top: 140px;
    font-style: normal; font-size: 15px; line-height: 22px; color: var(--ink);
  }
  .divider { position: absolute; left: 292px; top: 142px; width: 1px; height: 72px; background: var(--divider); }
  .contacts {
    position: absolute; left: 306px; top: 140px; list-style: none;
    font-size: 15px; line-height: 24px;
  }
  .contacts li { display: flex; align-items: center; gap: 8px; }
  .contacts svg { width: 13px; height: 13px; flex: none; }
  .icon-fill { fill: var(--muted); }
  .icon-line { fill: none; stroke: var(--muted); stroke-width: 2; }

  .waves { position: absolute; left: 0; top: 0; width: 640px; height: 366px; }

  .person { position: absolute; right: 60px; top: 298px; }
  .person__name { font-size: 22px; font-weight: 700; color: #fff; }
  .person__title { font-size: 17px; color: #fff; margin-left: 40px; }
</style>
</head>
<body>

<section class="card card--front" aria-label="Card front">
  <div class="texture" role="img" aria-label="Dark textured leather-look card surface"></div>
  <div class="wordmark"><span>BrindleStaffing</span><span class="wordmark__dot"></span></div>
  <p class="front-url">www.brindlestaffing.com</p>
</section>

<section class="card card--back" aria-label="Card back">
  <div class="texture" role="img" aria-label="Dark textured leather-look card surface"></div>

  <svg class="waves" viewBox="0 0 640 366" aria-hidden="true">
    <defs>
      <linearGradient id="band" x1="0" y1="0" x2="1" y2="0">
        <stop offset="0" stop-color="#f04a50"/>
        <stop offset="1" stop-color="#f37122"/>
      </linearGradient>
    </defs>
    <path d="M0 215 C 120 232, 210 300, 340 302 S 560 272, 640 282 L640 366 L0 366 Z" fill="url(#band)"/>
    <path d="M0 196 C 130 214, 215 286, 345 290 S 565 260, 640 270" fill="none" stroke="var(--brand-yellow)" stroke-width="5"/>
    <path d="M0 228 C 90 240, 150 272, 240 288" fill="none" stroke="var(--brand-yellow)" stroke-width="3"/>
  </svg>

  <div class="wordmark"><span>BrindleStaffing</span><span class="wordmark__dot"></span></div>

  <address class="address">
    417 39th Avenue South<br>
    Saint Petersburg FL 33712
  </address>

  <div class="divider"></div>

  <ul class="contacts">
    <li>
      <svg viewBox="0 0 24 24"><path class="icon-fill" d="M6.6 10.8a15 15 0 0 0 6.6 6.6l2.2-2.2a1 1 0 0 1 1-.25 11.4 11.4 0 0 0 3.6.6 1 1 0 0 1 1 1V20a1 1 0 0 1-1 1A17 17 0 0 1 3 4a1 1 0 0 1 1-1h3.5a1 1 0 0 1 1 1c0 1.25.2 2.45.6 3.6a1 1 0 0 1-.25 1z"/></svg>
      813-555-4172
    </li>
    <li>
      <svg viewBox="0 0 24 24"><path class="icon-line" d="M2 5h20v14H2z M2 5l10 8 10-8"/></svg>
      gpratley@brindlestaffing.com
    </li>
    <li>
      <svg viewBox="0 0 24 24"><circle class="icon-line" cx="12" cy="12" r="10"/><path class="icon-line" style="stroke-width:1.6" d="M2 12h20M12 2c3 3 3 17 0 20M12 2c-3 3-3 17 0 20"/></svg>
      www.brindlestaffing.com
    </li>
  </ul>

  <div class="person">
    <p class="person__name">Gordon Pratley</p>
    <p class="person__title">Chairman</p>
  </div>
</section>

</body>
</html>
```